Website redesign www.marigoldlawpc.com law firm site

Need to redesign the website that I currently have to look more modern and professional. Would also like to be able to make updates and post without having a huge hassle. See current www.marigoldlawpc.com. I just think that it looks very immature and it's very templated there's no ability for me to make posts or Add links or anything like that

Target Market(s)

California people looking for a powerhouse attorney in

Industry/Entity Type

Legal

Number of Pages Required

3 page

Font styles to use
Serif
Sans Serif

Colors
ec1f27
000000
ffffff

Requirements
Must have
• Must be mobile friendly. Must look professional and have ability to post links to other websites. Must have ability to post blogs or articles. Would like to be able to read my FeeTrove account and also have the ability to upload forms for people to download
Nice to have
• Simple design easy to use and not cluttered with too much text

```html
<!DOCTYPE html>
<html lang="en">
<head>
<meta charset="utf-8">
<title>Marigold Law P.C.</title>
<link rel="stylesheet" href="https://fonts.googleapis.com/css2?family=Cinzel:wght@400;700&family=Oswald:wght@400;500;600&family=Open+Sans:wght@400;600;700&display=swap">
<style>
:root{
  --red:#ec1f27;
  --black:#000000;
  --white:#ffffff;
  --ink:#222222;
  --muted:#6b6b6b;
  --line:#dddddd;
  --soft:#f1f1f1;
  --photo-a:#5a5550;
  --photo-b:#2a2624;
}
*{box-sizing:border-box;margin:0;padding:0}
html,body{width:1200px;height:2796px;overflow:hidden;background:var(--white)}
body{font-family:"Open Sans",Arial,sans-serif;color:var(--ink);font-size:14px;line-height:1.6}
.page{width:1200px;height:2796px;position:relative;overflow:hidden}

/* header */
.site-header{height:120px;display:flex;align-items:center;justify-content:space-between;padding:0 120px}
.brand{display:flex;align-items:center;gap:12px;font-family:"Oswald",sans-serif;font-weight:500;font-size:30px;letter-spacing:1px;text-transform:uppercase;color:var(--black);line-height:1}
.brand-mark{width:22px;height:22px;background:var(--red);display:block}
.contact-bar{display:flex;gap:40px;font-size:15px}
.contact-bar span{display:flex;align-items:center;gap:10px}
.icon-dot{width:26px;height:26px;border-radius:50%;background:var(--red);display:inline-flex;align-items:center;justify-content:center}

.main-nav{height:32px;background:var(--black);display:flex;justify-content:center}
.main-nav a{color:var(--white);text-decoration:none;font-family:"Oswald",sans-serif;font-size:15px;letter-spacing:1px;text-transform:uppercase;padding:0 32px;line-height:32px}
.main-nav a.active{background:var(--red)}

/* hero */
.hero{position:relative;height:410px}
.hero-photo{position:absolute;inset:0;background:linear-gradient(120deg,#8d8a86 0%,var(--photo-a) 35%,#a7a19a 60%,var(--photo-b) 100%)}
.hero-arrow{position:absolute;top:190px;width:26px;height:30px;background:rgba(0,0,0,.6);display:flex;align-items:center;justify-content:center}
.hero-arrow.left{left:0}.hero-arrow.right{right:0}
.tagline{height:80px;background:#1a1a1a;color:var(--white);font-family:"Cinzel",serif;font-size:20px;text-align:center;padding:12px 180px;line-height:1.35}

/* welcome */
.welcome{padding:40px 160px 0;display:flex;gap:40px;height:340px}
.section-title{display:flex;align-items:center;gap:14px;font-family:"Oswald",sans-serif;font-weight:500;font-size:30px;text-transform:uppercase;letter-spacing:1px;color:var(--black)}
.section-title em{font-style:normal;color:var(--red)}
.title-rule{width:60px;height:3px;background:var(--red);margin:8px 0 16px 60px}
.welcome-text{flex:1}
.welcome-text p{font-size:12.5px;color:var(--muted);margin-bottom:10px}
.btn{display:inline-block;font-family:"Oswald",sans-serif;text-transform:uppercase;font-size:13px;letter-spacing:1px;padding:7px 14px;background:#d9d9d9;color:var(--ink)}
.btn-red{background:var(--red);color:var(--white)}
.profile{width:200px;text-align:center}
.profile-photo{width:200px;height:220px;background:linear-gradient(160deg,#b99a82,#4a3a32);border:4px solid var(--red)}
.profile figcaption{font-size:12px;margin-top:6px}

/* practice */
.practice{height:630px;background:linear-gradient(180deg,#1c1c1c,#2b2020 50%,#141414);padding:40px 160px 0}
.practice .section-title{color:var(--white);justify-content:center}
.practice .title-rule{margin:8px auto 26px}
.practice-grid{display:grid;grid-template-columns:repeat(3,1fr);gap:30px 40px}
.practice-card{background:var(--white)}
.practice-photo{height:170px}
.practice-card h3{height:38px;display:flex;align-items:center;gap:10px;padding:0 14px;font-family:"Oswald",sans-serif;font-weight:400;font-size:15px;text-transform:uppercase;color:var(--ink)}
.practice-card h3 i{width:14px;height:14px;background:var(--red);display:inline-block}
.practice .cta{text-align:center;margin-top:26px}

/* account + inquiry */
.split{height:370px;display:flex;gap:60px;padding:36px 160px 0}
.account{flex:1.3}
.account p{font-size:12.5px;color:var(--muted);margin-bottom:12px}
.inquiry{flex:1}
.inquiry .field{height:30px;border:1px solid var(--line);margin-bottom:8px;font-size:12px;color:#999;padding:5px 10px}
.inquiry .field.tall{height:60px}

/* blog */
.blog{height:470px;background:var(--soft);padding:36px 160px 0}
.blog .section-title{justify-content:center}
.blog .title-rule{margin:8px auto 26px}
.blog-grid{display:grid;grid-template-columns:repeat(3,1fr);gap:40px}
.blog-card{background:var(--white)}
.blog-photo{height:170px;position:relative}
.date-badge{position:absolute;left:50%;bottom:-18px;transform:translateX(-50%);width:50px;height:46px;background:var(--red);color:var(--white);text-align:center;font-family:"Oswald",sans-serif;font-size:18px;line-height:1.1;padding-top:4px}
.date-badge small{display:block;font-size:11px}
.blog-body{padding:26px 14px 14px}
.blog-meta{font-size:11px;color:#999;margin-bottom:6px}
.blog-body h4{font-size:15px;font-weight:700;margin-bottom:4px}
.blog-body p{font-size:12px;color:var(--muted)}

/* footer */
.site-footer{height:330px;background:var(--black);color:#cfcfcf;padding:36px 160px 0;display:grid;grid-template-columns:1fr 1.3fr 1.2fr 1fr;gap:30px;font-size:12.5px}
.site-footer h5{font-family:"Oswald",sans-serif;font-weight:500;font-size:18px;color:var(--white);margin-bottom:12px}
.site-footer ul{list-style:none}
.site-footer li{margin-bottom:4px}
.site-footer li::before{content:"› ";color:var(--red)}
.news-input{height:30px;background:var(--white);color:#999;padding:5px 10px;margin:10px 0 8px}
.socials{display:flex;gap:6px;margin-top:12px}
.socials i{width:24px;height:24px;background:#333;display:block}
.map{height:170px;background:linear-gradient(135deg,#d9e4cf,#b8c7d6)}
.copyright{position:absolute;bottom:0;left:0;right:0;height:36px;background:var(--red);color:var(--white);text-align:center;font-size:12px;line-height:36px}
</style>
</head>
<body>
<div class="page">

<header class="site-header">
  <div class="brand"><i class="brand-mark"></i>Marigold Law P.C.</div>
  <div class="contact-bar">
    <span><i class="icon-dot"><svg width="14" height="14" viewBox="0 0 24 24"><path fill="#fff" d="M6.6 10.8a15 15 0 0 0 6.6 6.6l2.2-2.2c.3-.3.7-.4 1-.2 1.1.4 2.3.6 3.6.6.6 0 1 .4 1 1V20c0 .6-.4 1-1 1A17 17 0 0 1 3 4c0-.6.4-1 1-1h3.5c.6 0 1 .4 1 1 0 1.3.2 2.5.6 3.6.1.3 0 .7-.2 1z"/></svg></i>(555) 014-2870</span>
    <span><i class="icon-dot"><svg width="14" height="14" viewBox="0 0 24 24"><path fill="#fff" d="M3 5h18v14H3z"/><path fill="none" stroke="#ec1f27" stroke-width="2" d="M3 6l9 7 9-7"/></svg></i>dana@marigoldlawpc.com</span>
  </div>
</header>

<nav class="main-nav">
  <a class="active" href="#">Home</a><a href="#">Attorney Profile</a><a href="#">Practice Areas ▾</a><a href="#">Client Reviews</a><a href="#">Links</a><a href="#">Contact Us</a>
</nav>

<section class="hero">
  <div class="hero-photo" role="img" aria-label="Attorney in a suit signing papers beside a small model house"></div>
  <span class="hero-arrow left"><svg width="10" height="14"><path d="M8 1L2 7l6 6" stroke="#fff" stroke-width="2" fill="none"/></svg></span>
  <span class="hero-arrow right"><svg width="10" height="14"><path d="M2 1l6 6-6 6" stroke="#fff" stroke-width="2" fill="none"/></svg></span>
</section>
<div class="tagline">A Boutique Law Firm Opportunity For Clients Who Want To Enjoy All The Advantages of Dana's Broad Legal Experience And Education.</div>

<section class="welcome">
  <div class="welcome-text">
    <h2 class="section-title"><svg width="44" height="36" viewBox="0 0 44 36"><path d="M22 4v28M8 32h28M6 10h32M6 10l-5 12h10zM38 10l-5 12h10z" stroke="#333" stroke-width="2" fill="none"/></svg>Welcome to <em>MarigoldLawPC</em></h2>
    <div class="title-rule"></div>
    <p>Find the big firm style legal counsel you can work with in your hometown region of Marigold Law P.C. in Alderton, CA. Attorney Dana R. Marlow offers a boutique law firm opportunity for clients who want to enjoy all the advantages of her broad legal experience and education.</p>
    <p>She works closely with clients, and has the knowledge of many areas of law to apply to your situation. This is very helpful when it is necessary to incorporate several different areas of law into creating a winning argument for your unique case.</p>
    <a class="btn" href="#">Read More ›</a>
  </div>
  <figure class="profile">
    <div class="profile-photo" role="img" aria-label="Portrait photo of the attorney"></div>
    <figcaption>Dana R. Marlow</figcaption>
  </figure>
</section>

<section class="practice">
  <h2 class="section-title"><svg width="40" height="34" viewBox="0 0 44 36"><path d="M22 4v28M8 32h28M6 10h32M6 10l-5 12h10zM38 10l-5 12h10z" stroke="#fff" stroke-width="2" fill="none"/></svg>Practice <em>Areas</em></h2>
  <div class="title-rule"></div>
  <div class="practice-grid">
    <article class="practice-card"><div class="practice-photo" role="img" aria-label="Business people shaking hands" style="background:linear-gradient(135deg,#c7ccd2,#4d5560)"></div><h3><i></i>Business Law</h3></article>
    <article class="practice-card"><div class="practice-photo" role="img" aria-label="Model house with keys on paperwork" style="background:linear-gradient(135deg,#d8cfc4,#6a5a4a)"></div><h3><i></i>Real Estate Law</h3></article>
    <article class="practice-card"><div class="practice-photo" role="img" aria-label="Bankruptcy document with a gavel" style="background:linear-gradient(135deg,#e6dccf,#7a3a2a)"></div><h3><i></i>Bankruptcy</h3></article>
    <article class="practice-card"><div class="practice-photo" role="img" aria-label="Family holding hands" style="background:linear-gradient(135deg,#d6c4b3,#8a6a52)"></div><h3><i></i>Family Law</h3></article>
    <article class="practice-card"><div class="practice-photo" role="img" aria-label="Handcuffs and gavel on a desk" style="background:linear-gradient(135deg,#9a9a9a,#2e2e2e)"></div><h3><i></i>Criminal Law</h3></article>
    <article class="practice-card"><div class="practice-photo" role="img" aria-label="Gavel and scales of justice" style="background:linear-gradient(135deg,#c9a77a,#4a3222)"></div><h3><i></i>Civil Litigation</h3></article>
  </div>
  <div class="cta"><a class="btn btn-red" href="#">View All Practice Areas ›</a></div>
</section>

<section class="split">
  <div class="account">
    <h2 class="section-title"><svg width="40" height="34" viewBox="0 0 44 36"><path d="M22 4v28M8 32h28M6 10h32M6 10l-5 12h10zM38 10l-5 12h10z" stroke="#333" stroke-width="2" fill="none"/></svg>FeeTrove <em>Account</em></h2>
    <div class="title-rule"></div>
    <p>Clients can review invoices, make secure payments and check the balance of their account online at any time. Our payment portal keeps your records organized and accessible, so you always know where your case stands and what has been settled.</p>
    <p>Forms needed for your matter can be downloaded from this page and returned to our office by mail or in person. Please contact us if you have any questions about your account or need help finding a document.</p>
    <a class="btn" href="#">Read More ›</a>
  </div>
  <div class="inquiry">
    <h2 class="section-title"><svg width="40" height="34" viewBox="0 0 44 36"><path d="M22 4v28M8 32h28M6 10h32M6 10l-5 12h10zM38 10l-5 12h10z" stroke="#333" stroke-width="2" fill="none"/></svg>Quick <em>Inquiry</em></h2>
    <div class="title-rule"></div>
    <div class="field">Your Name</div>
    <div class="field">Email</div>
    <div class="field">Phone</div>
    <div class="field tall">Your Message Here</div>
    <a class="btn btn-red" href="#">Submit</a>
  </div>
</section>

<section class="blog">
  <h2 class="section-title"><svg width="40" height="34" viewBox="0 0 44 36"><path d="M22 4v28M8 32h28M6 10h32M6 10l-5 12h10zM38 10l-5 12h10z" stroke="#333" stroke-width="2" fill="none"/></svg>Latest <em>Blog</em></h2>
  <div class="title-rule"></div>
  <div class="blog-grid">
    <article class="blog-card"><div class="blog-photo" role="img" aria-label="Lawyer meeting with clients" style="background:linear-gradient(135deg,#c5c0ba,#4a4440)"><span class="date-badge">07<small>May</small></span></div>
      <div class="blog-body"><div class="blog-meta">Admin · 2 Comments</div><h4>Planning for a new business</h4><p>Simple steps to protect your company from the very first day of trading.</p></div></article>
    <article class="blog-card"><div class="blog-photo" role="img" aria-label="Criminal law book with gavel" style="background:linear-gradient(135deg,#b98a6a,#3a2418)"><span class="date-badge">07<small>May</small></span></div>
      <div class="blog-body"><div class="blog-meta">Admin · 2 Comments</div><h4>Know your rights in court</h4><p>What to expect before your first hearing and how to prepare with counsel.</p></div></article>
    <article class="blog-card"><div class="blog-photo" role="img" aria-label="Hands cupped around a small paper family" style="background:linear-gradient(135deg,#e2dcd4,#8a7a6a)"><span class="date-badge">07<small>May</small></span></div>
      <div class="blog-body"><div class="blog-meta">Admin · 2 Comments</div><h4>Family matters made clear</h4><p>Answers to common questions about custody, support and shared property.</p></div></article>
  </div>
</section>

<footer class="site-footer">
  <div>
    <h5>Quick Link</h5>
    <ul><li>Home</li><li>About Us</li><li>Practice Areas</li><li>Reviews</li><li>Blog</li><li>Links</li><li>Contact Us</li></ul>
  </div>
  <div>
    <h5>Join Our Newsletter</h5>
    <p>Subscribe to our newsletter to get the latest legal news and firm updates.</p>
    <div class="news-input">Enter Your Email</div>
    <a class="btn btn-red" href="#">Subscribe</a>
    <div class="socials"><i></i><i></i><i></i><i></i></div>
  </div>
  <div>
    <h5>Contact Detail</h5>
    <p>214 Orchard Street, Suite 300<br>Alderton, CA 95000</p>
    <p style="margin-top:8px">(555) 014-2870</p>
    <p>dana@marigoldlawpc.com</p>
    <p>www.marigoldlawpc.com</p>
  </div>
  <div>
    <div class="map" role="img" aria-label="Map showing the office location"></div>
  </div>
</footer>
<div class="copyright">Copyright © 2016 Marigold Law P.C. All Right Reserved.</div>

</div>
</body>
</html>
```